Birchline Septic Solutions

Would like to see some single sided ones but would also like to see some double sided with one sided only being the logo. Owners name is Colin Vandro. Phone number is 555-214-0387
Services are pumping, inspections, installs, and repairs

Contact Information for Business Card

555-241-0387 Colin Vandro Ashmere Vale, OH

```html
<!DOCTYPE html>
<html lang="en">
<head>
<meta charset="UTF-8">
<title>Birchline Septic Solutions – Business Cards</title>
<link href="https://fonts.googleapis.com/css2?family=Lato:wght@400;700;900&display=swap" rel="stylesheet">
<style>
  :root {
    --stage: #2a2a2a;
    --card-black: #050505;
    --card-white: #ffffff;
    --teal: #2cbdb9;
    --ink: #0b0b0b;
    --paper-text: #ffffff;
  }
  * { box-sizing: border-box; margin: 0; padding: 0; }
  html, body { width: 1200px; height: 875px; overflow: hidden; }
  body {
    background: var(--stage);
    font-family: "Lato", sans-serif;
    position: relative;
  }
  .card {
    position: absolute;
    top: 287px;
    width: 520px;
    height: 300px;
    border-radius: 18px;
    overflow: hidden;
  }
  .card--front { left: 55px; background: var(--card-black); color: var(--paper-text); }
  .card--back { left: 625px; background: var(--card-white); color: var(--ink); }

  .brand-name {
    font-family: "Lato", sans-serif;
    font-weight: 900;
    text-transform: uppercase;
    text-align: center;
    line-height: 1.05;
    white-space: nowrap;
  }
  .card--front .brand-name {
    position: absolute;
    top: 88px; left: 0; right: 0;
    font-size: 40px;
    letter-spacing: 3px;
    color: var(--paper-text);
  }
  .card--front .brand-name span { display: block; font-size: 20px; letter-spacing: 8px; margin-top: 6px; }
  .services {
    position: absolute;
    top: 218px; left: 0; right: 0;
    text-align: center;
    font-size: 15px;
    font-weight: 400;
    letter-spacing: 0.3px;
    white-space: nowrap;
  }

  .card--back .brand-name {
    position: absolute;
    top: 48px; left: 0; right: 0;
    font-size: 34px;
    letter-spacing: 3px;
    color: var(--ink);
  }
  .card--back .brand-name span { display: block; font-size: 16px; letter-spacing: 7px; margin-top: 6px; }

  .contact-band {
    position: absolute;
    left: 0; right: 0; bottom: 0;
    height: 120px;
    background: var(--teal);
    border-top: 4px solid var(--ink);
    display: flex;
    align-items: center;
    padding: 0 30px;
  }
  .owner-name {
    font-weight: 900;
    font-size: 30px;
    letter-spacing: 0.5px;
    text-transform: uppercase;
    color: var(--ink);
    flex: 1;
    text-align: center;
    white-space: nowrap;
  }
  .divider { width: 1px; height: 46px; background: var(--ink); margin: 0 20px; flex: none; }
  .contact-list { list-style: none; display: flex; flex-direction: column; gap: 4px; flex: none; }
  .contact-list li { display: flex; align-items: center; gap: 8px; color: var(--ink); white-space: nowrap; }
  .contact-list .location { font-size: 15px; font-weight: 400; }
  .contact-list .phone { font-size: 19px; font-weight: 900; }
  .icon { width: 14px; height: 14px; flex: none; }
</style>
</head>
<body>
  <section class="card card--front" aria-label="Card front">
    <div class="brand-name">Birchline<span>Septic Solutions</span></div>
    <p class="services">Pumping, Inspections, Installs &amp; Repairs</p>
  </section>

  <section class="card card--back" aria-label="Card back">
    <div class="brand-name">Birchline<span>Septic Solutions</span></div>
    <div class="contact-band">
      <h1 class="owner-name">Colin Vandro</h1>
      <span class="divider"></span>
      <ul class="contact-list">
        <li class="location">
          <svg class="icon" viewBox="0 0 24 24" aria-hidden="true"><path d="M12 2a7 7 0 0 0-7 7c0 5 7 13 7 13s7-8 7-13a7 7 0 0 0-7-7zm0 9.5A2.5 2.5 0 1 1 12 6.5a2.5 2.5 0 0 1 0 5z" fill="currentColor"/></svg>
          Ashmere Vale, OH
        </li>
        <li class="phone">
          <svg class="icon" viewBox="0 0 24 24" aria-hidden="true"><path d="M6.6 10.8a15.1 15.1 0 0 0 6.6 6.6l2.2-2.2a1 1 0 0 1 1-.25 11.4 11.4 0 0 0 3.6.57 1 1 0 0 1 1 1V20a1 1 0 0 1-1 1A17 17 0 0 1 3 4a1 1 0 0 1 1-1h3.5a1 1 0 0 1 1 1c0 1.25.2 2.45.57 3.57a1 1 0 0 1-.25 1z" fill="currentColor"/></svg>
          555-241-0387
        </li>
      </ul>
    </div>
  </section>
</body>
</html>
```